Business Card Design Project - del varosi group

dear Sirs

we need business card design for our group ( DEL Varosi Group ) , i have got the Logo design of our group from pixel harbor in previous , so all need details relating to our group i think available with you, as well as the the chosen logo design

we hope to provide us with business card logo that to be appropaite and satisfactory to us .

thanks

note : logo design of our group is attached .
Updates

Reason: please extend the deadline of my project for additional 15 days because i didn't received appropriate design for our gruop yet . kindly beaware that i have received 77 design till now , supossed to send me 200-250 design at least . thanks

Target Market(s)

contents

name : Kerem EL Nadiri

position : Operation Manager

Industry/Entity Type

Business

Requirements
Must have

• person name

group logo
Nice to have
• logo color matching with back background

```html
<!DOCTYPE html>
<html lang="en">
<head>
<meta charset="utf-8">
<title>DEL Varosi Group – Business Card</title>
<link rel="stylesheet" href="https://fonts.googleapis.com/css2?family=Open+Sans:wght@400;600;700&display=swap">
<style>
  :root {
    --bg: #e9e6e2;
    --card-white: #ffffff;
    --brand-blue: #0a72c2;
    --brand-navy: #1a4e8e;
    --band-dark: #0d5aa6;
    --text-grey: #5f6266;
    --rule-grey: #c9cbce;
  }
  * { box-sizing: border-box; margin: 0; padding: 0; }
  html, body { width: 1200px; height: 758px; overflow: hidden; }
  body {
    background: var(--bg);
    font-family: "Open Sans", Arial, sans-serif;
    position: relative;
  }
  .card {
    position: absolute;
    top: 229px;
    width: 520px;
    height: 300px;
    border-radius: 24px;
    overflow: hidden;
    box-shadow: 0 6px 18px rgba(0,0,0,0.18);
  }
  .card-front { left: 60px; background: var(--card-white); }
  .card-back { left: 620px; background: var(--brand-blue); }

  /* Front */
  .front-logo {
    position: absolute; left: 38px; top: 34px;
    display: flex; align-items: center; gap: 12px;
  }
  .logo-square { width: 26px; height: 26px; background: var(--brand-navy); }
  .logo-name {
    font-weight: 700; font-size: 34px; letter-spacing: 0.5px;
    color: var(--brand-navy); text-transform: uppercase; line-height: 1;
  }
  .person {
    position: absolute; left: 150px; top: 116px;
    font-size: 17px; color: var(--brand-navy); font-weight: 700;
  }
  .person .role { font-weight: 400; font-size: 13px; color: var(--text-grey); }
  .address {
    position: absolute; left: 150px; top: 168px; width: 112px;
    text-align: right; font-size: 12.5px; line-height: 18px; color: var(--text-grey);
  }
  .divider {
    position: absolute; left: 276px; top: 150px; width: 1px; height: 70px;
    background: var(--rule-grey);
  }
  .contacts {
    position: absolute; left: 286px; top: 148px; list-style: none;
    font-size: 12.5px; line-height: 18px; color: var(--text-grey);
  }
  .contacts li { display: flex; align-items: center; gap: 6px; }
  .contacts svg { width: 10px; height: 10px; fill: var(--text-grey); }
  .front-bands { position: absolute; left: 0; bottom: 0; width: 520px; height: 78px; }
  .front-web {
    position: absolute; right: 28px; bottom: 34px;
    color: #fff; font-size: 13px; letter-spacing: 2px;
  }

  /* Back */
  .back-logo {
    position: absolute; left: 0; right: 0; top: 104px;
    display: flex; justify-content: center; align-items: center; gap: 14px;
  }
  .back-logo .logo-square { background: #fff; width: 30px; height: 30px; }
  .back-logo .logo-name { color: #fff; font-size: 38px; }
  .back-web {
    position: absolute; left: 0; right: 0; top: 208px; text-align: center;
    color: #fff; font-size: 17px; letter-spacing: 2.5px;
  }
</style>
</head>
<body>
  <section class="card card-front" aria-label="Business card front">
    <div class="front-logo">
      <span class="logo-square"></span>
      <span class="logo-name">DEL Varosi Group</span>
    </div>
    <p class="person">Kerem EL Nadiri, <span class="role">Operation Manager</span></p>
    <p class="address">Street name, City<br>State, zip code</p>
    <div class="divider"></div>
    <ul class="contacts">
      <li><svg viewBox="0 0 10 10"><rect x="2.5" y="0" width="5" height="10" rx="1"/></svg>+2348105550142</li>
      <li><svg viewBox="0 0 10 10"><path d="M1 1h3l1 2.5-1.5 1a6 6 0 0 0 3 3l1-1.5L9 6v3C4 9 1 6 1 1z"/></svg>+2348105550142</li>
      <li><svg viewBox="0 0 10 10"><rect x="1" y="3" width="8" height="5" rx="1"/><rect x="3" y="0.5" width="4" height="3"/></svg>+2348105550142</li>
      <li><svg viewBox="0 0 10 10"><path d="M0 2h10v6H0z"/></svg>name@ravelinhotels.com</li>
    </ul>
    <svg class="front-bands" viewBox="0 0 520 78" preserveAspectRatio="none" aria-hidden="true">
      <rect x="0" y="50" width="520" height="28" fill="var(--brand-blue)"/>
      <polygon points="285,22 520,22 520,50 272,50" fill="var(--band-dark)"/>
      <polygon points="265,50 270,38 285,22 290,22 274,50" fill="#fff"/>
    </svg>
    <span class="front-web">www.website.com</span>
  </section>

  <section class="card card-back" aria-label="Business card back">
    <div class="back-logo">
      <span class="logo-square"></span>
      <span class="logo-name">DEL Varosi Group</span>
    </div>
    <p class="back-web">www.website.com</p>
  </section>
</body>
</html>
```